Modern Label for cleaning products for the brand Vorlix

We need a label design for our line of cleaning products. The label should feature our logo and an image to identify the product's intended use. I've added our logo and an image for use. This only concerns the design of the label on the front of the bottle.

Label dimensions:
Label 1 (500ml bottle with spray): width 58mm x height 115mm
Label 2: (1L bottle): width 73mm x height 140mm
The design must be consistent for both bottles which you find in the pictures.

The bottles to be labeled are white. See the attachment for a photo of the bottles.

The photo must also appear on the label to identify the product's intended use.

Product information:
Brand: Vorlix
Product: Sanitary Cleaner

This text must be placed on the label:
"Cleans, descales & freshens. followed with this text: "Ideal for quick and powerful cleaning. A ready-to-use product for everyday use."

- Mention the seperate USP's: Sanitary, Bathroom, Toilet, Wet areas

Appearance: This is a consumer product, but it must have a professional appearance. We would like to see a design that use the color blue from our logo.

Target Market(s)

Consumers who take care of their homes and want to maintain it the correct (professional) way

Font styles to use
Sans Serif

Colors
0054AA
0677BA
7BADD7
CADEEF
E8F1F8

Requirements
Must have
• USP's + use of image and logo + blend in 1 design
Nice to have
• Keep the color of the logo in the design
Should not have
• Comic sans

```html
<!DOCTYPE html>
<html lang="en">
<head>
<meta charset="utf-8">
<title>Vorlix Sanitary Cleaner – Front Label</title>
<link rel="stylesheet" href="https://fonts.googleapis.com/css2?family=Archivo:wdth,wght@62..125,300..900&display=swap">
<style>
  :root {
    --blue-deep: #0054aa;
    --blue-main: #0677ba;
    --blue-bright: #0a8fd6;
    --blue-soft: #7badd7;
    --blue-pale: #cadeef;
    --blue-mist: #e8f1f8;
    --teal: #2fcfc0;
    --teal-soft: #7fe3da;
    --ink: #111418;
    --white: #ffffff;
  }
  * { margin: 0; padding: 0; box-sizing: border-box; }
  html, body {
    width: 1200px; height: 898px; overflow: hidden;
    background: var(--white);
    font-family: "Archivo", Arial, sans-serif;
    font-stretch: 125%;
  }
  .label {
    position: absolute; left: 425px; top: 100px;
    width: 357px; height: 703px;
    border-radius: 14px; overflow: hidden;
    background: var(--white);
    box-shadow: 0 0 0 1px #e3e7ea;
  }
  .label > * { position: absolute; }
  .top-swoosh { left: 0; top: 0; width: 357px; height: 60px; }
  .claim-badge {
    left: 16px; top: 29px; width: 82px; height: 57px;
    border-radius: 0 0 4px 4px;
    background: linear-gradient(160deg, var(--teal-soft), var(--teal));
    color: var(--blue-deep);
    font-weight: 800; font-size: 9.4px; line-height: 9.8px;
    text-align: center; padding-top: 19px; letter-spacing: -0.2px;
  }
  .claim-badge .amp { font-size: 6.5px; }
  .brand-dot {
    left: 144px; top: 42px; width: 84px; height: 84px; border-radius: 50%;
    background: radial-gradient(circle at 40% 35%, var(--blue-bright), var(--blue-main));
  }
  .scene-photo {
    left: 0; top: 170px; width: 357px; height: 302px;
    background:
      linear-gradient(180deg, rgba(255,255,255,1) 0%, rgba(255,255,255,0) 20%),
      linear-gradient(90deg, #8a8d8f 0%, #a9abad 30%, #d9dbdc 48%, #eef0f2 65%, #f4f5f6 100%);
  }
  .scene-photo::after {
    content: ""; position: absolute; left: 0; right: 0; bottom: 0; height: 80px;
    background: linear-gradient(180deg, rgba(150,150,150,0) 0%, #9a9a99 60%, #8f8f8e 100%);
  }
  .brand-name {
    left: 0; width: 357px; top: 136px; z-index: 2;
    text-align: center; font-weight: 800; font-size: 46px; line-height: 50px;
    color: var(--ink); letter-spacing: -1px; font-stretch: 100%;
  }
  .ready-tag {
    left: 210px; top: 236px; padding: 1px 7px;
    background: var(--blue-main); color: var(--white);
    border-radius: 7px; font-size: 7.4px; font-weight: 500; letter-spacing: 0.1px;
  }
  .ready-text {
    left: 197px; width: 118px; top: 249px;
    text-align: center; color: var(--ink);
    font-weight: 800; font-size: 12px; line-height: 12px; letter-spacing: -0.3px;
  }
  .bottom-panel { left: 0; top: 405px; width: 357px; height: 298px; }
  .product-name {
    left: 0; width: 357px; top: 470px; text-align: center; color: var(--white);
  }
  .product-name .main {
    display: block; font-weight: 900; font-size: 46px; line-height: 44px; letter-spacing: -2.5px;
  }
  .product-name .sub {
    display: block; font-weight: 400; font-size: 27px; line-height: 26px; letter-spacing: 0.5px;
  }
  .suitable-tag {
    left: 35px; top: 550px; width: 80px; height: 12px; border-radius: 6px;
    background: var(--white); color: var(--blue-deep);
    font-size: 7px; font-weight: 800; text-align: center; line-height: 12px;
  }
  .usp-list { left: 30px; top: 573px; width: 300px; list-style: none; }
  .usp {
    position: absolute; width: 80px; margin-left: -40px;
    text-align: center; color: var(--white); font-size: 8px; font-weight: 500;
  }
  .usp svg { display: block; margin: 0 auto 6px; width: 32px; height: 32px; fill: var(--white); }
  .usp.bathroom { left: 47px; } .usp.toilet { left: 113px; }
  .usp.wet { left: 179px; } .usp.sanitary { left: 254px; }
  .benefit-band {
    left: 0; top: 638px; width: 357px; height: 48px;
    background: linear-gradient(90deg, var(--teal) 0%, #2aa8d6 45%, rgba(10,143,214,0) 75%);
  }
  .benefit-text {
    left: 0; width: 245px; top: 643px; text-align: center; color: var(--white);
    font-size: 12.5px; line-height: 12px; font-weight: 800; letter-spacing: -0.4px;
  }
  .benefit-text .lead { display: block; font-weight: 400; font-size: 10px; line-height: 11px; letter-spacing: 0.3px; }
  .volume { left: 282px; top: 641px; color: var(--white); white-space: nowrap; }
  .volume .amount {
    display: inline-block; font-size: 32px; font-weight: 400; line-height: 30px;
    transform: scaleX(0.62); transform-origin: left; margin-right: -21px; letter-spacing: -1px;
  }
  .volume .unit { font-size: 7px; }
  .volume .net { display: block; font-size: 9.5px; line-height: 9px; letter-spacing: 0.3px; }
</style>
</head>
<body>
<article class="label">
  <svg class="top-swoosh" viewBox="0 0 357 60" preserveAspectRatio="none">
    <defs>
      <linearGradient id="swooshBlue" x1="0" x2="1">
        <stop offset="0" stop-color="#0054aa"/><stop offset="0.5" stop-color="#0677ba"/><stop offset="1" stop-color="#0a8fd6"/>
      </linearGradient>
    </defs>
    <path d="M0 0H357V13C250 8 120 15 0 52Z" fill="url(#swooshBlue)"/>
    <path d="M0 52C120 15 250 8 357 13V11C250 6 120 13 0 50Z" fill="#cadeef"/>
  </svg>

  <div class="claim-badge">CLEANS,<br>DESCALES <span class="amp">&amp;</span><br>FRESHENS</div>

  <div class="brand-dot"></div>

  <div class="scene-photo" role="img" aria-label="Photo of a clean modern bathroom with a glass shower, white vanity with mirror and a tiled bathtub"></div>

  <div class="brand-name">vorlix</div>

  <div class="ready-tag">A READY-TO-USE</div>
  <div class="ready-text">PRODUCT FOR<br>EVERYDAY USE.</div>

  <svg class="bottom-panel" viewBox="0 0 357 298" preserveAspectRatio="none">
    <defs>
      <linearGradient id="panelBlue" x1="0" y1="0" x2="1" y2="1">
        <stop offset="0" stop-color="#0677ba"/><stop offset="0.6" stop-color="#0a8fd6"/><stop offset="1" stop-color="#0677ba"/>
      </linearGradient>
      <linearGradient id="stripeTeal" x1="0" x2="1">
        <stop offset="0" stop-color="#e8f1f8"/><stop offset="0.5" stop-color="#7fe3da"/><stop offset="1" stop-color="#2fcfc0"/>
      </linearGradient>
    </defs>
    <path d="M0 60C140 58 270 40 357 5V298H0Z" fill="url(#panelBlue)"/>
    <path d="M0 58C140 56 270 36 357 0V6C270 42 140 60 0 62Z" fill="url(#stripeTeal)"/>
    <path d="M0 62C140 60 270 43 357 8V12C270 46 140 62 0 64Z" fill="#cadeef" opacity="0.6"/>
  </svg>

  <h1 class="product-name"><span class="main">SANITARY</span><span class="sub">CLEANER</span></h1>

  <div class="suitable-tag">SUITABLE FOR</div>
  <ul class="usp-list">
    <li class="usp bathroom">
      <svg viewBox="0 0 32 32"><path d="M16 2a4 4 0 0 1 4 4v8h-2.5V6a1.5 1.5 0 0 0-3 0v2H12V6a4 4 0 0 1 4-4Z"/><path d="M2 15h28v3c0 5-4 9-9 9h-1v4h-8v-4c-5-1-10-5-10-9Z"/></svg>
      BATHROOM
    </li>
    <li class="usp toilet">
      <svg viewBox="0 0 32 32"><rect x="8" y="1" width="16" height="10" rx="2"/><path d="M6 13h20c0 5-3 8-6 9l1 8H11l1-8c-3-1-6-4-6-9Z"/></svg>
      TOILET
    </li>
    <li class="usp wet">
      <svg viewBox="0 0 32 32"><path d="M13 4c5 7 9 12 9 17a9 9 0 0 1-18 0c0-5 4-10 9-17Z"/><path d="M24 3c3 4 5 7 5 9.5a5 5 0 0 1-10 0C19 10 21 7 24 3Z"/></svg>
      WET AREAS
    </li>
    <li class="usp sanitary">
      <svg viewBox="0 0 32 32"><path d="M4 12l3-1 2 5 0-9h3l1 9 2-7 3 1-2 9v6l-3 6H7l-2-8Z"/><path d="M19 14l3-11 3 1-1 7 3-5 3 2-4 8-4 6h-3Z"/></svg>
      SANITARY
    </li>
  </ul>

  <div class="benefit-band"></div>
  <p class="benefit-text"><span class="lead">IDEAL FOR</span>QUICK AND POWERFUL<br>CLEANING.</p>

  <div class="volume"><span class="amount">500</span><span class="unit">ML</span><span class="net">NET WT</span></div>
</article>
</body>
</html>
```